Visualisation Software brochure

i need a sales brochure for a new visualisation software company called Lumora Studio Max.
The software has been specifically designed for manufacturers, distributers and retailers in the design / décor / furnishing / building industries. It allows customers can then import unlimited numbers of digital photos of rooms from their own home or take advantage of a library of pre-made photos, and then render different products from your catalogue into that photo to see what the finished look will be.
i have attached:
1) a mock up of the home page of the website
2) example of brochure wording that i have put together (although i am a little unsure about what other words i can add - so any suggestions here would be good)
3) i have attached some examples of other brochures that i like and would like similar designs
I am after a classy brochure used by a large corporate technology company that is given to executives and gives an impression of quality, trustworthiness and innovation.
• the colour blue as per the colours on my website mock up provided in the design brief
• I like simple, smart, clean and uncluttered design
• I like simple, clean and uncluttered design
• I like pictures that fit in with my technology (whether that be home and interior design, mixing virtual world and real world, visualising an idea) rather than basic stock of corporate people
Updates
Target Market(s)
marketing professionals
Industry/Entity Type
Software
Font styles to use
Look and feel
Each slider illustrates characteristics of the customer's brand and the style your logo design should communicate.

```html
<!DOCTYPE html>
<html lang="en">
<head>
<meta charset="utf-8">
<title>Lumora Studio Max – Brochure</title>
<link href="https://fonts.googleapis.com/css2?family=Source+Sans+3:wght@400;600&display=swap" rel="stylesheet">
<style>
:root{
  --blue:#2d4f94;
  --blue-dark:#1f3a78;
  --text:#3a3a3c;
  --panel-grey:#e7e8ea;
  --band-grey:#8d8f93;
  --white:#ffffff;
  --rule:#6b6d70;
  --frame:#b8babd;
}
*{margin:0;padding:0;box-sizing:border-box}
html,body{width:1200px;height:852px;overflow:hidden;background:var(--white)}
body{font-family:"Source Sans 3",Arial,sans-serif;color:var(--text);position:relative}
.abs{position:absolute}
h2{font-weight:400;color:var(--blue);font-size:19px;line-height:21px}
p{font-size:9.9px;line-height:13.9px;letter-spacing:-0.12px;text-align:justify;margin-bottom:7px}
ul{list-style:none}
li{font-size:9.9px;line-height:13.9px;letter-spacing:-0.12px;position:relative;padding-left:9px;margin-bottom:6px}
li::before{content:"";position:absolute;left:0;top:6px;width:3px;height:3px;border-radius:50%;background:var(--blue)}

.photo-tablet-man{left:0;top:0;width:258px;height:322px;
  background:radial-gradient(ellipse 45% 60% at 45% 45%,#8e9aa6 0%,#aab8c6 45%,rgba(200,214,228,0) 75%),
             linear-gradient(135deg,#e9eef4 0%,#c6d5e4 55%,#9cb4cc 100%)}
.challenge-panel{left:0;top:322px;width:258px;height:486px;background:var(--panel-grey);padding:14px 10px 0 28px}
.challenge-panel h2{margin-bottom:9px}
.challenge-panel p{margin-bottom:6px}
.footer-band{left:0;top:808px;width:258px;height:44px;background:var(--band-grey)}

.brand{left:278px;top:26px;display:flex;align-items:center;gap:10px}
.brand-dot{width:32px;height:32px;border-radius:50%;background:var(--blue)}
.brand-name{font-size:12px;color:var(--blue-dark);font-weight:400}
.header-rule{left:442px;top:42px;width:294px;height:1.5px;background:var(--rule);z-index:2}

.solution{left:278px;top:86px;width:282px}
.solution h2{margin-bottom:12px}
.photo-hologram{left:278px;top:322px;width:358px;height:226px;
  background:radial-gradient(ellipse 30% 55% at 50% 40%,#6e6a6a 0%,#9aa0a8 50%,rgba(210,215,222,0) 85%),
             linear-gradient(180deg,#e4e7eb 0%,#c3c9d0 55%,#7f8892 100%)}
.solution-more{left:278px;top:551px;width:282px}

.photo-team{left:598px;top:0;width:602px;height:357px;
  background:radial-gradient(ellipse 55% 50% at 55% 35%,#d8c2b0 0%,rgba(216,194,176,0) 70%),
             linear-gradient(120deg,#e6ecf2 0%,#9fb3ca 40%,#3e5a84 75%,#2c4166 100%)}
.benefits-title{left:647px;top:12px;font-size:25px;color:var(--white);font-weight:400;z-index:2}

.retail-tab{left:636px;top:322px;width:274px;height:36px;background:var(--white);padding:13px 0 0 28px}
.retail-panel{left:636px;top:357px;width:564px;height:191px;background:var(--white);padding:6px 24px 0 26px}
.retail-panel li{margin-bottom:4.5px}

.consumer-panel{left:598px;top:548px;width:602px;height:304px;border-top:1px solid var(--frame);border-left:1px solid var(--frame);background:var(--white)}
.consumer-title{left:664px;top:563px}
.consumer-col-a{left:657px;top:596px;width:246px}
.consumer-col-b{left:925px;top:562px;width:250px}
.photo-laptop-group{left:606px;top:690px;width:590px;height:148px;
  background:radial-gradient(ellipse 50% 60% at 50% 70%,#b9a89a 0%,rgba(185,168,154,0) 80%),
             linear-gradient(180deg,rgba(255,255,255,0) 0%,#eceef1 35%,#d3d9e0 100%)}
</style>
</head>
<body>

<div class="abs photo-tablet-man" role="img" aria-label="Businessman looking at a tablet in front of a glowing world map interface"></div>

<section class="abs challenge-panel">
  <h2>The challenge for both customers and retailers</h2>
  <p>Gone are the days when all you needed was a showroom, a product line, and a business card. Customers are better informed, more interactive, and more selective than ever before. With access to a range of new technologies and a wide variety of online resources, these connected consumers are increasingly demanding a dynamic, seamless, integrated, consistent, accessible and personalised experience with your brand across all online, bricks-and-mortar and mobile channels.</p>
  <p>The customer must be empowered to interact across all touchpoints and channels; they want to browse and buy on their own schedules and retailers must offer equally accurate and immediate access to products and customer service. Consumers want to be inspired and be given the tools, advice and confidence to create unique, personal spaces - meaning companies need to feed this design dream and appealing to their vision is essential. The shopping experience should be built around the new reality that most consumers make their browsing and purchasing commitments online, often before they ever see the product in person.</p>
  <p>Amid ongoing economic uncertainty, true omni-channel retailers need to continue to focus on understanding the customer psyche and leveraging innovation to drive loyalty and customer engagement and ultimately increase sales.</p>
</section>
<div class="abs footer-band"></div>

<div class="abs brand"><span class="brand-dot"></span><span class="brand-name">Lumora Studio Max</span></div>

<section class="abs solution">
  <h2>The virtualised solution</h2>
  <p>Having your own branded virtual design software embedded on your website or accessible via a Robotix and/or Pomelo app will help bridge the gap between your customers' design dreams and your products. Our software helps solve one of the biggest problems many experience whilst redecorating or designing their home, which is despite looking at numerous samples, most cannot visualise or conceptualise what the finished look will be.</p>
  <p>It doesn't matter what business you're in. Your customers will be able to visualise all possible product combinations for their new home – it just depends on your range. The software can easily handle 'flat surface products' including roofing, cladding, garage doors, windows and driveways/pathways to interior products such as carpet, tiles, timber and laminate flooring, doors, art works, bench tops and splashbacks.</p>
</section>

<div class="abs photo-hologram" role="img" aria-label="Man framing floating holographic screens showing room designs"></div>

<section class="abs solution-more">
  <p>Importantly, our technology can also handle any product in 3D - whether it be furniture, lighting, floor rugs, curtains / blinds, wardrobes, household items, kitchen cabinets and bathroom fixtures. A truly unique feature allows customers to simply delete the existing item from their photo and replace it with another product from your catalogue without removing any item physically.</p>
  <p>Today's consumer doesn't just rely on technological gimmicks such as augmented reality or one in-store visit before making important investment decisions. With so much competition in the marketplace consumers are more driven than ever to shop around with the amount and quality of value-adding service the real deal breaker rather than price.</p>
  <p>It has become more about initiating the education of your customer versus waiting for them to ask for assistance. Using our technology can increase sales conversion rates as once customers have identified what products they would like to purchase they come to you as educated buyers, already having experienced a fantastic customer interaction with your brand.</p>
</section>

<div class="abs photo-team" role="img" aria-label="Business team around a table with glowing network icons overlaid"></div>
<div class="abs header-rule"></div>
<div class="abs benefits-title">Benefits</div>

<div class="abs retail-tab"><h2>Retailer Benefits:</h2></div>
<section class="abs retail-panel">
  <ul>
    <li>Be the market innovator and leader by combining technology and a dynamic, seamless, integrated and consistent level of customer service across all online, bricks-and-mortar and mobile channels that delivers the big wow factor</li>
    <li>Extend your reach - don't limit your technology footprint by only using Pomelo apps - our solution leverages and optimises all mobile devices and desktops (PomOS, Robotix, Web). This equates to a larger watershed of customers and more sales</li>
    <li>Increase brand engagement as our bespoke and scalable visualisation application will help customers build a relationship with your company, brand, and products and then share that experience within their social circles</li>
    <li>Understand buyer behaviour by receiving real usage statistics to obtain valuable insight about your customers and conduct trend analysis to determine how your future strategies can further enhance your bottom-line</li>
    <li>Increased sales to further grow your business</li>
    <li>Maximise the exposure of your products by uploading your entire product catalogue into a visualisation software that makes them look real</li>
  </ul>
</section>

<div class="abs consumer-panel"></div>
<h2 class="abs consumer-title">Consumer Benefits:</h2>
<ul class="abs consumer-col-a">
  <li>Reduce your customer's purchase anxiety as they will have the knowledge that the products they are choosing from your range are the right choice</li>
  <li>Greater flexibility in the way they shop by being open 24/7 and being able to engage with your brand when they want and how they want. Happier customers and hence more sales.</li>
</ul>
<ul class="abs consumer-col-b">
  <li>An easy-to-use interface along with guided help and tutorials for those less confident with technology</li>
  <li>Being able to make informed purchasing decisions as they can easily compare a large range of your products at the touch of a computer key</li>
  <li>Improved personalised buying experience by enabling customers to use photos of their own personal spaces and incorporate your products</li>
</ul>
<div class="abs photo-laptop-group" role="img" aria-label="Five cheerful young people with laptops, some raising their arms"></div>

</body>
</html>
```